Business card for medical clinic

I need an upmarket, modern medical/health business card for my clinic

Contact Information for Business Card

name, address, email, qr code

```html
<!DOCTYPE html>
<html lang="en">
<head>
<meta charset="utf-8">
<title>Aldera Care Clinic — Business Card</title>
<link rel="stylesheet" href="https://fonts.googleapis.com/css2?family=Montserrat:wght@600&family=Roboto:wght@400&display=swap">
<style>
  :root {
    --page-bg: #d9d6d4;
    --card-face: #eceae9;
    --navy: #17233b;
    --blue: #1f8fc4;
    --blue-deep: #1a5f88;
    --icon-blue: #2a8fc0;
    --text-light: #e4e8ec;
    --logo-ink: #1b4a66;
  }
  * { margin: 0; padding: 0; box-sizing: border-box; }
  html, body { width: 1200px; height: 969px; overflow: hidden; }
  body { background: var(--page-bg); position: relative; font-family: "Roboto", sans-serif; }

  .card {
    position: absolute; left: 100px; top: 200px;
    width: 1000px; height: 570px;
    border-radius: 34px; overflow: hidden;
    background: var(--card-face);
    box-shadow: 0 10px 30px rgba(0,0,0,0.15);
  }
  .card-shapes { position: absolute; inset: 0; }

  .brand {
    position: absolute; left: 40px; top: 232px;
    display: flex; align-items: center; gap: 18px;
  }
  .brand-circle {
    width: 92px; height: 92px; border-radius: 50%;
    border: 5px solid var(--logo-ink);
  }
  .brand-name {
    font-family: "Roboto", sans-serif; font-weight: 400;
    font-size: 34px; line-height: 1.15; letter-spacing: 2px;
    color: var(--logo-ink); text-transform: uppercase;
  }

  .person {
    position: absolute; right: 123px; top: 64px; text-align: right;
    color: var(--text-light);
  }
  .person-name { font-family: "Montserrat", sans-serif; font-weight: 600; font-size: 34px; letter-spacing: 0.5px; line-height: 1.1; }
  .person-role { font-size: 21px; letter-spacing: 0.5px; margin-top: 4px; }

  .icon-box {
    position: absolute; width: 52px; height: 52px; border-radius: 5px;
    display: flex; align-items: center; justify-content: center;
  }
  .icon-box.is-light { background: var(--icon-blue); }
  .icon-box.is-dark { background: var(--navy); }
  .icon-box svg { width: 30px; height: 30px; }

  .contact-lines {
    position: absolute; color: var(--text-light);
    font-size: 23px; line-height: 32px; white-space: nowrap;
  }
  .phones { left: 628px; top: 210px; }
  .web { left: 614px; top: 306px; font-size: 25px; }
  .address { right: 123px; top: 452px; text-align: right; font-size: 25px; }
</style>
</head>
<body>
  <div class="card">
    <svg class="card-shapes" viewBox="0 0 1000 570" width="1000" height="570">
      <defs>
        <linearGradient id="panelTone" x1="0" y1="0" x2="1" y2="0">
          <stop offset="0" stop-color="#1f8fc4"/>
          <stop offset="0.55" stop-color="#1a5f88"/>
          <stop offset="1" stop-color="#17233b"/>
        </linearGradient>
        <linearGradient id="bandTone" x1="0" y1="0" x2="1" y2="0">
          <stop offset="0" stop-color="#238fc6"/>
          <stop offset="1" stop-color="#1e86b8"/>
        </linearGradient>
      </defs>
      <rect x="571" y="0" width="429" height="570" fill="url(#panelTone)"/>
      <polygon points="533,0 571,0 571,570 533,570 533,423 497,401 497,172 533,149" fill="#17233b"/>
      <rect x="497" y="176" width="503" height="219" fill="url(#bandTone)"/>
    </svg>

    <div class="brand">
      <div class="brand-circle"></div>
      <div class="brand-name">Aldera Care<br>Clinic</div>
    </div>

    <div class="person">
      <div class="person-name">DANIEL REEVE</div>
      <div class="person-role">GRAPHIC DESIGNER</div>
    </div>
    <div class="icon-box is-light" style="left:906px; top:66px;">
      <svg viewBox="0 0 24 24"><circle cx="12" cy="8" r="4.5" fill="#fff"/><path d="M3.5 22c0-5 3.8-8 8.5-8s8.5 3 8.5 8z" fill="#fff"/></svg>
    </div>

    <div class="icon-box is-dark" style="left:533px; top:211px;">
      <svg viewBox="0 0 24 24"><path d="M6.6 3.5l2.6-.6 1.6 4.3-1.8 1.3c.8 2.3 2.4 4.5 4.3 6l1.9-1.1 3 3.3-1.7 2.2c-5.6-.6-10.4-7.8-9.9-15.4z" fill="#fff"/></svg>
    </div>
    <div class="contact-lines phones">+0044 - 2718 - 30562<br>+0044 - 2718 - 30579</div>

    <div class="icon-box is-dark" style="left:533px; top:306px;">
      <svg viewBox="0 0 24 24"><rect x="3" y="4" width="18" height="12" rx="1" fill="#fff"/><rect x="5" y="6" width="14" height="8" fill="#17233b"/><rect x="10.5" y="16" width="3" height="3" fill="#fff"/><rect x="7.5" y="19" width="9" height="1.6" fill="#fff"/></svg>
    </div>
    <div class="contact-lines web">hello@alderacare-mail.com<br>www.alderacare.com</div>

    <div class="contact-lines address">48 Linden Park Avenue,<br>Harbor District 204</div>
    <div class="icon-box is-light" style="left:906px; top:453px;">
      <svg viewBox="0 0 24 24"><path d="M12 3L1.5 12l1.3 1.5L12 5.6l9.2 7.9 1.3-1.5z" fill="#fff"/><path d="M5 13v8h5v-5h4v5h5v-8l-7-6z" fill="#fff"/></svg>
    </div>
  </div>
</body>
</html>
```